Visitenkarten und Briefpapier
Zielgruppe
Planung und Realisierung von individuellen und wertbeständigen Kamin- und Ofenlösungen, sowie Fliesen- und Baddesign.
Aufgabenstellung
Wir benötigen ein möglichst schlichtes Design für Visitenkarten, bzw. Briefpapier. Für die Visitenkarten gerne auch Vorschläge mit Prägung, Ausstanzung oder mit Heißfolie. Auch Klappkarten wären denkbar. Das Design soll "das gewisse Etwas haben" und nicht zu verspielt sein.
Die Visitenkarten sind für die Firma KORVA, das Logo von der Ausstellung "raumfunke" soll dezent mit eingebunden werden (bei dem Briefpapier z.B. in der Fußzeile". Die farbliche Gestaltung sollte sich an den Farben des Logos orientieren.
Schriftart für Texte: Century Gothic
Schriftfarbe: RAL 7016
Nur eine Idee: Ich könnte mir auch gut vorstellen, dass die Visitenkarte aus einer Zündholzverpackung (wenn dann aber eine besondere mit nur einem Zündholz oder einem besonders breiten) besteht: http://glimmvelo.de/produkte_briefchen.php

```html
<!DOCTYPE html>
<html lang="de">
<head>
<meta charset="utf-8">
<title>KORVA – Visitenkarte</title>
<link rel="stylesheet" href="https://fonts.googleapis.com/css2?family=Questrial&display=swap">
<style>
  :root {
    --backdrop: #d6a05c;
    --card: #c9a77f;
    --panel: #22333b;
    --ink: #2b3238;
    --ink-soft: #3a4248;
    --paper-text: #f1ece4;
    --mirror: #6f6a63;
  }
  * { box-sizing: border-box; margin: 0; padding: 0; }
  html, body { width: 1200px; height: 1120px; overflow: hidden; }
  body {
    background: var(--backdrop);
    font-family: "Questrial", "Century Gothic", sans-serif;
    color: var(--ink);
    position: relative;
  }
  .card {
    position: absolute;
    left: 150px;
    width: 602px;
    height: 390px;
    background: var(--card);
    overflow: hidden;
  }
  .card--front { top: 52px; }
  .card--back { top: 534px; }

  .panel {
    position: absolute;
    top: 0;
    height: 100%;
    background: var(--panel);
    color: var(--paper-text);
  }
  .card--front .panel { left: 0; width: 220px; }
  .card--back .panel { right: 0; width: 221px; }

  .contact {
    position: absolute;
    left: 21px;
    bottom: 14px;
    font-size: 16.5px;
    line-height: 21px;
  }
  .contact .label { display: inline-block; width: 44px; }
  .contact .mail { margin-top: 4px; }

  .face {
    position: absolute;
    inset: 0;
  }
  .face--mirrored {
    transform: scaleX(-1);
    color: var(--mirror);
  }
  .brand {
    position: absolute;
    right: 34px;
    top: 16px;
    text-align: right;
  }
  .brand-name {
    font-size: 66px;
    line-height: 66px;
    letter-spacing: 3px;
    font-weight: 400;
  }
  .brand-tagline {
    font-size: 18.5px;
    letter-spacing: 0.3px;
    margin-top: -2px;
  }
  .person {
    position: absolute;
    right: 34px;
    top: 174px;
    text-align: right;
  }
  .person-name { font-size: 33px; line-height: 36px; color: var(--ink-soft); }
  .card--back .person-name { color: inherit; }
  .person-role { font-size: 15px; }
  .web {
    position: absolute;
    right: 22px;
    bottom: 12px;
    font-size: 16.5px;
  }

  .partner {
    position: absolute;
    right: 27px;
    bottom: 32px;
    font-size: 21px;
    color: #b9bcbd;
  }
</style>
</head>
<body>

  <section class="card card--front" aria-label="Visitenkarte Vorderseite">
    <div class="panel">
      <address class="contact" style="font-style:normal">
        <div>Am Lindenhang 4c</div>
        <div>35812 Wendbach</div>
        <div><span class="label">fon:</span>05417 / 38 14 60</div>
        <div><span class="label">fax:</span>05417 / 38 14 66</div>
        <div class="mail">info@korva-wendbach.de</div>
      </address>
    </div>
    <div class="face">
      <div class="brand">
        <div class="brand-name">KORVA</div>
        <div class="brand-tagline">kamine · öfen · fliesen</div>
      </div>
      <div class="person">
        <div class="person-name">Jannik Sorell</div>
        <div class="person-role">Geschäftsführer</div>
      </div>
      <div class="web">www.korva-wendbach.de</div>
    </div>
  </section>

  <section class="card card--back" aria-label="Visitenkarte Rückseite">
    <div class="face face--mirrored" aria-hidden="true">
      <div class="brand">
        <div class="brand-name">KORVA</div>
        <div class="brand-tagline">kamine · öfen · fliesen</div>
      </div>
      <div class="person">
        <div class="person-name">Jannik Sorell</div>
        <div class="person-role">Geschäftsführer</div>
      </div>
      <div class="web">www.korva-wendbach.de</div>
    </div>
    <div class="panel">
      <div class="partner">raumfunke</div>
    </div>
  </section>

</body>
</html>
```